Creating a website for a life changing company (Halvra Q)

We do need a website for our Coaching and Consulting business we recently launched. We do need it for information purposes and that our clients do have the opportunity to subscribe for packages, programs etc.
We would like to see designs which use the colours blue and yellow (see attachment). The final design should communicate our passion for the potential in people and the benefit (rising onward) for them.
Updates
Additional information:
Our company (webpage): Halvra Q (the C stands for "what people cannot see / imagine now...)
Welcome to Halvra Q(uarry)
Consulting (O.R.T.) & Coaching (Rise onward)
Two pillars:
1) O.R.T. ( Steward pathway - Our program - focussing on companies - business orientated)
2) Rise onward (Daily renewal - Events - focusing on individuals - primarily life changing)
For both of them we offer: Lanternhall & Halvra Q+ (This should go as a subscription)
Eventually you can draft this as a rhombus
Industry/Entity Type
Coaching / Consulting
Coding
Coded - Design and coding required
Number of Pages Required
1 page
Font styles to use
Other font styles liked:
- Lato
Requirements
Must have
- Please see attachment (About us / Offers / Calendar function / Links to Instagram and LinkedIn account / mailing list / page for clients
Nice to have
- A banner

```html
<!DOCTYPE html>
<html lang="en">
<head>
<meta charset="utf-8">
<title>Halvra Q – Coaching &amp; Consulting</title>
<link href="https://fonts.googleapis.com/css2?family=Lato:wght@300;400;700;900&display=swap" rel="stylesheet">
<style>
:root{
  --navy:#264d73;
  --navy-deep:#203f5f;
  --yellow:#f8cd38;
  --ink:#4a4a4a;
  --muted:#6b6b6b;
  --pale-blue:#e3ecf4;
  --pale-grey:#f3f5f7;
  --white:#ffffff;
}
*{box-sizing:border-box;margin:0;padding:0}
html,body{width:1200px;height:4812px;overflow:hidden}
body{font-family:'Lato',sans-serif;color:var(--ink);background:var(--white);position:relative}
.abs{position:absolute}
.center{text-align:center}
.btn{position:absolute;display:flex;align-items:center;justify-content:center;border-radius:30px;font-weight:700;font-size:15px;color:var(--white);text-transform:uppercase}
.btn-navy{background:var(--navy)}
.btn-yellow{background:var(--yellow)}
.section-title{position:absolute;left:0;width:1200px;text-align:center;font-size:30px;font-weight:700;color:var(--navy);text-transform:uppercase;letter-spacing:.5px}

/* header */
.site-header{position:absolute;left:0;top:0;width:1200px;height:128px;background:var(--white)}
.brand{position:absolute;left:104px;top:44px;display:flex;align-items:center;gap:10px;font-weight:700;font-size:20px;color:var(--navy);letter-spacing:3px}
.brand-dot{width:14px;height:14px;border-radius:50%;background:var(--yellow)}
.contact-top{position:absolute;top:16px;display:flex;align-items:center;gap:12px;font-size:15px;font-weight:700;color:var(--navy)}
.icon-round{width:46px;height:46px;border-radius:50%;background:var(--navy);display:flex;align-items:center;justify-content:center}
.main-nav{position:absolute;top:84px;left:350px;display:flex;gap:38px;font-size:13px;font-weight:700;color:#222;text-transform:uppercase}
.main-nav .active{color:var(--navy)}

/* hero */
.hero{position:absolute;left:0;top:128px;width:1200px;height:714px;background:linear-gradient(100deg,#2d3a34 0%,#7a6660 30%,#b8a79c 50%,#d9dde2 75%,#c9d3dc 100%)}
.hero-badge{position:absolute;left:669px;top:144px;width:472px;height:472px;border-radius:50%;background:rgba(248,205,56,.93)}
.hero-title{position:absolute;left:669px;top:256px;width:472px;text-align:center;font-size:52px;font-weight:700;color:var(--navy)}
.hero-text{position:absolute;left:715px;top:337px;width:380px;text-align:center;font-size:15px;line-height:28px;color:var(--navy)}
.hero-dots span{position:absolute;left:1157px;width:10px;height:10px;border-radius:50%;background:#2a2a2a}

/* about */
.about-photo{position:absolute;left:143px;top:910px;width:498px;height:521px;border-radius:42px;background:linear-gradient(160deg,#3c4a55,#7b8894 55%,#2d3f5c)}
.about-title{position:absolute;left:700px;top:955px;font-size:34px;font-weight:700;color:var(--navy)}
.about-text{position:absolute;left:698px;top:1062px;width:360px;font-size:12.5px;line-height:24px;color:var(--muted);text-align:justify;font-family:Arial,sans-serif}

/* programs */
.programs{position:absolute;left:0;top:1504px;width:1200px;height:608px;background:var(--pale-blue)}
.program{position:absolute;top:0;width:300px;text-align:center}
.program-photo{width:174px;height:174px;border-radius:50%;margin:191px auto 0}
.program h3{margin-top:20px;font-size:21px;font-weight:700;color:var(--navy);text-transform:uppercase}
.program p{margin-top:12px;font-size:13px;line-height:25px;color:var(--muted);font-family:Arial,sans-serif}

/* calendar */
.calendar-band{position:absolute;left:0;top:2112px;width:1200px;height:724px;background:linear-gradient(180deg,#2a4c6d,#294a6a 60%,#23425f)}
.calendar-card{position:absolute;left:278px;top:2281px;width:644px;height:497px;background:#f2f2f2}
.cal-year{position:absolute;top:2330px;font-size:16px;color:var(--navy)}
.cal-month{position:absolute;left:278px;width:644px;top:2325px;text-align:center;font-size:23px;font-weight:700;color:#444}
.cal-row{position:absolute;left:330px;width:540px;display:grid;grid-template-columns:repeat(7,1fr);text-align:center;font-size:13px;color:#222}
.cal-head{font-size:18px;font-weight:700;color:#333}
.today{display:inline-block;width:28px;height:28px;line-height:28px;border-radius:50%;background:var(--navy);color:var(--white)}
.cal-btn{position:absolute;top:2698px;height:40px;display:flex;align-items:center;justify-content:center;gap:8px;font-size:11px;color:var(--white);text-transform:uppercase}

/* offer */
.offer{position:absolute;left:0;top:2836px;width:1200px;height:425px;background:var(--yellow)}
.offer-word{position:absolute;left:160px;top:176px;width:310px;text-align:center;font-size:72px;font-weight:700;color:var(--white)}
.deal{position:absolute;left:533px;width:490px;text-align:center;color:var(--white)}
.deal-rule{position:absolute;left:533px;width:490px;height:1px;background:rgba(255,255,255,.85)}

/* pricing */
.price-card{position:absolute;top:3458px;width:306px;height:440px;background:var(--white);box-shadow:0 0 14px rgba(0,0,0,.08);text-align:center}
.price-card h3{margin-top:32px;font-size:20px;font-weight:700;color:var(--navy)}
.price-card .sub{margin-top:10px;font-size:13.5px;color:var(--muted);font-family:Arial,sans-serif}
.price{margin-top:14px;font-size:62px;font-weight:400;color:var(--navy);line-height:70px}
.price sup{font-size:20px;vertical-align:top;position:relative;top:-6px}
.price small{font-size:14px}
.features{list-style:none;text-align:left;margin:22px 0 0 38px;font-size:13.5px;color:var(--muted);font-family:Arial,sans-serif}
.features li{display:flex;align-items:center;gap:18px;height:41px}

/* newsletter */
.newsletter{position:absolute;left:0;top:3975px;width:1200px;height:401px;background:var(--pale-grey)}
.email-field{position:absolute;left:218px;top:4205px;width:764px;height:50px;border:1px solid #c9c9c9;border-radius:26px;background:var(--white);padding-left:24px;display:flex;align-items:center;font-size:13px;color:#333}

/* footer */
.site-footer{position:absolute;left:0;top:4376px;width:1200px;height:436px;background:var(--navy)}
.footer-brand{position:absolute;left:0;width:1200px;top:4460px;display:flex;justify-content:center;align-items:center;gap:14px;font-size:30px;font-weight:700;color:var(--white);letter-spacing:6px}
.footer-nav{position:absolute;left:0;width:1200px;top:4592px;display:flex;justify-content:center;gap:38px;font-size:13px;font-weight:700;color:var(--white);text-transform:uppercase}
.footer-contact{position:absolute;top:4652px;display:flex;align-items:center;gap:18px;color:var(--white);font-size:16px;line-height:24px}
.ring{width:44px;height:44px;border-radius:50%;border:1.5px solid var(--white);display:flex;align-items:center;justify-content:center;flex:none}
.copyright{position:absolute;left:0;width:1200px;top:4738px;text-align:center;font-size:15px;color:var(--white)}
</style>
</head>
<body>

<header class="site-header">
  <div class="brand"><span class="brand-dot"></span>HALVRA Q</div>
  <div class="contact-top" style="left:508px">
    <span class="icon-round"><svg width="18" height="14" viewBox="0 0 18 14"><rect x="1" y="1" width="16" height="12" rx="2" fill="#fff"/><path d="M1.5 2l7.5 6 7.5-6" stroke="#264d73" stroke-width="1.6" fill="none"/></svg></span>
    Email : info@halvraq.com
  </div>
  <div class="contact-top" style="left:822px">
    <span class="icon-round"><svg width="18" height="18" viewBox="0 0 24 24"><path fill="#fff" d="M6.6 10.8a15.1 15.1 0 006.6 6.6l2.2-2.2a1 1 0 011-.25 11.4 11.4 0 003.6.57 1 1 0 011 1V20a1 1 0 01-1 1A17 17 0 013 4a1 1 0 011-1h3.5a1 1 0 011 1c0 1.25.2 2.45.57 3.57a1 1 0 01-.25 1z"/></svg></span>
    Call Us : +1 555 014 2290
  </div>
  <nav class="main-nav">
    <span class="active">Home</span><span>About Us</span><span>O.R.T.</span><span>Lanternhall</span><span>Rise Onward</span><span>Halvra Q+</span><span>Testimonials</span>
  </nav>
</header>

<section class="hero" role="img" aria-label="Photo of a smiling woman in conversation with a client in a bright office"></section>
<div class="hero-badge"></div>
<h1 class="hero-title">HALVRA Q</h1>
<p class="hero-text">Sed ut perspiciatis unde omnis iste natus error sit voluptatem accusantium doloremque laudantium totam rem aperiam, eaque ipsa quae ab inventore beatae vitae dicta sunt explicabo</p>
<div class="btn btn-navy" style="left:819px;top:600px;width:173px;height:56px;font-size:17px">Read More</div>
<div class="hero-dots"><span style="top:635px"></span><span style="top:655px;background:var(--yellow)"></span><span style="top:675px"></span></div>

<section>
  <div class="about-photo" role="img" aria-label="Portrait of the founder in a blue suit leaning on a railing"></div>
  <h2 class="about-title">ABOUT MAREN</h2>
  <p class="about-text">Sed ut perspiciatis unde omnis iste natus error sit volupta tem accusantium doloremque laudantium, totam rem aper iam, eaque ipsa quae ab illo inventore veritatis et quasi arc hitecto beatae vitae dicta sunt explicabo. Nemo enim ipsam voluptatem quia voluptas sit aspernatur aut odit aut fugit, sed quia consequuntur magni dolores eos qui ratione volu ptatem sequi nesciunt. Neque porro quisquam est, qui dolo rem ipsum quia dolor sit amet, consectetur, adipisci velit, sed quia non numquam eius modi tempora incidunt ut magnam aliquam quaerat voluptatem. Ut enim ad minima nisi ut aliquid ex ea commodi consequatur</p>
  <div class="btn btn-navy" style="left:698px;top:1350px;width:148px;height:45px">Read More</div>
</section>

<section class="programs">
  <h2 class="section-title" style="top:72px">Programs</h2>
  <div class="program" style="left:125px">
    <div class="program-photo" role="img" aria-label="Photo of a coach guiding a colleague at a laptop" style="background:linear-gradient(150deg,#d7dde3,#6f7f8e)"></div>
    <h3>Coaching</h3>
    <p>Nemo enim ipsam voluptatem quia<br>voluptas sit aspernatur aut odit aut fugit<br>voluptatem sequi nesciunt</p>
  </div>
  <div class="program" style="left:450px">
    <div class="program-photo" role="img" aria-label="Photo of a team meeting around a table" style="background:linear-gradient(150deg,#8c8f92,#3b3f44)"></div>
    <h3>Consulting</h3>
    <p>Nemo enim ipsam voluptatem quia<br>voluptas sit aspernatur aut odit aut fugit<br>voluptatem sequi nesciunt</p>
  </div>
  <div class="program" style="left:775px">
    <div class="program-photo" role="img" aria-label="Photo of a person on a video call at a laptop" style="background:linear-gradient(150deg,#c9ccd0,#354a6b)"></div>
    <h3>Fireside Chat</h3>
    <p>Nemo enim ipsam voluptatem quia<br>voluptas sit aspernatur aut odit aut fugit<br>voluptatem sequi nesciunt</p>
  </div>
  <div class="btn btn-navy" style="left:208px;top:508px;width:134px;height:45px">Read More</div>
  <div class="btn btn-yellow" style="left:533px;top:508px;width:134px;height:45px">Read More</div>
  <div class="btn btn-navy" style="left:858px;top:508px;width:134px;height:45px">Read More</div>
</section>

<section class="calendar-band" role="img" aria-label="Soft blue backdrop of a person looking over a misty landscape"></section>
<h2 class="section-title" style="top:2176px;color:var(--white)">Calendar Function</h2>
<div class="calendar-card"></div>
<span class="cal-year" style="left:352px">2021</span>
<div class="cal-month">SEPTEMBER, 2022</div>
<span class="cal-year" style="left:815px">2023</span>
<div class="cal-row cal-head" style="top:2412px"><span>SUN</span><span>MON</span><span>TUE</span><span>WED</span><span>THUR</span><span>FRI</span><span>SAT</span></div>
<div class="cal-row" style="top:2472px"><span>1</span><span>2</span><span>3</span><span>4</span><span>5</span><span>6</span><span>7</span></div>
<div class="cal-row" style="top:2507px;line-height:28px"><span>8</span><span><span class="today">9</span></span><span>10</span><span>11</span><span>12</span><span>13</span><span>14</span></div>
<div class="cal-row" style="top:2554px"><span>15</span><span>16</span><span>17</span><span>18</span><span>19</span><span>20</span><span>21</span></div>
<div class="cal-row" style="top:2595px"><span>22</span><span>23</span><span>24</span><span>25</span><span>26</span><span>27</span><span>28</span></div>
<div class="cal-row" style="top:2636px"><span>29</span><span>30</span><span>31</span><span></span><span></span><span></span><span></span></div>
<svg class="abs" style="left:322px;top:2533px" width="18" height="18" viewBox="0 0 18 18"><circle cx="9" cy="9" r="7.5" fill="none" stroke="#444" stroke-width="1.5"/><path d="M10.5 5.5L7 9l3.5 3.5" stroke="#444" stroke-width="1.5" fill="none"/></svg>
<svg class="abs" style="left:869px;top:2533px" width="18" height="18" viewBox="0 0 18 18"><circle cx="9" cy="9" r="7.5" fill="none" stroke="#444" stroke-width="1.5"/><path d="M7.5 5.5L11 9l-3.5 3.5" stroke="#444" stroke-width="1.5" fill="none"/></svg>
<div class="cal-btn" style="left:413px;width:153px;background:var(--navy)">See Planned Events
  <svg width="11" height="11" viewBox="0 0 12 12"><circle cx="5" cy="5" r="3.6" fill="none" stroke="#fff" stroke-width="1.6"/><path d="M7.6 7.6L11 11" stroke="#fff" stroke-width="1.6"/></svg></div>
<div class="cal-btn" style="left:635px;width:152px;background:var(--yellow)">Set Reminder
  <svg width="11" height="11" viewBox="0 0 12 12"><circle cx="6" cy="6" r="6" fill="#fff"/><path d="M6 3v6M3 6h6" stroke="#f8cd38" stroke-width="1.6"/></svg></div>

<section class="offer">
  <div class="offer-word">OFFER</div>
  <div class="deal" style="top:116px;font-size:44px;font-weight:300">DEAL OF THE DAY</div>
  <div class="deal-rule" style="top:176px"></div>
  <div class="deal" style="top:188px;font-size:66px;font-weight:700">FLAT 70% OFF</div>
  <div class="deal-rule" style="top:272px"></div>
  <div class="deal" style="top:284px;font-size:18px">LIFE-CHANGING COACHING &amp; CONSULTING BUSINESS</div>
</section>

<section>
  <h2 class="section-title" style="top:3340px">Pricing Packages</h2>
  <div class="price-card" style="left:112px">
    <h3>RISE ONWARD LIGHT</h3>
    <p class="sub">Sed ut perspiciatis unde omnis iste</p>
    <div class="price"><sup>$</sup>49<small>/hd</small></div>
    <ul class="features">
      <li><svg width="14" height="12" viewBox="0 0 14 12"><path d="M1.5 6.5l4 4 7-9" stroke="#264d73" stroke-width="2.4" fill="none"/></svg>Nemo enim ipsam voluptatem</li>
      <li><svg width="14" height="12" viewBox="0 0 14 12"><path d="M1.5 6.5l4 4 7-9" stroke="#264d73" stroke-width="2.4" fill="none"/></svg>Quia voluptas sit aspernatur</li>
      <li><svg width="14" height="12" viewBox="0 0 14 12"><path d="M1.5 6.5l4 4 7-9" stroke="#264d73" stroke-width="2.4" fill="none"/></svg>Aut odit aut fugit, sed quia</li>
    </ul>
    <div class="btn btn-navy" style="left:78px;top:346px;width:150px;height:46px">Signup</div>
  </div>
  <div class="price-card" style="left:446px">
    <h3>RISE ONWARD (2-3 DAYS)</h3>
    <p class="sub">Sed ut perspiciatis unde omnis iste</p>
    <div class="price" style="color:var(--yellow)"><sup>$</sup>59<small style="color:var(--navy)">/day</small></div>
    <ul class="features">
      <li><svg width="14" height="12" viewBox="0 0 14 12"><path d="M1.5 6.5l4 4 7-9" stroke="#f8cd38" stroke-width="2.4" fill="none"/></svg>Nemo enim ipsam voluptatem</li>
      <li><svg width="14" height="12" viewBox="0 0 14 12"><path d="M1.5 6.5l4 4 7-9" stroke="#f8cd38" stroke-width="2.4" fill="none"/></svg>Quia voluptas sit aspernatur</li>
      <li><svg width="14" height="12" viewBox="0 0 14 12"><path d="M1.5 6.5l4 4 7-9" stroke="#f8cd38" stroke-width="2.4" fill="none"/></svg>Aut odit aut fugit, sed quia</li>
    </ul>
    <div class="btn btn-yellow" style="left:78px;top:346px;width:150px;height:46px">Signup</div>
  </div>
  <div class="price-card" style="left:780px">
    <h3>RISE ONWARD UNLIMITED</h3>
    <p class="sub">Sed ut perspiciatis unde omnis iste</p>
    <div class="price"><sup>$</sup>69<small>/lw</small></div>
    <ul class="features">
      <li><svg width="14" height="12" viewBox="0 0 14 12"><path d="M1.5 6.5l4 4 7-9" stroke="#264d73" stroke-width="2.4" fill="none"/></svg>Nemo enim ipsam voluptatem</li>
      <li><svg width="14" height="12" viewBox="0 0 14 12"><path d="M1.5 6.5l4 4 7-9" stroke="#264d73" stroke-width="2.4" fill="none"/></svg>Quia voluptas sit aspernatur</li>
      <li><svg width="14" height="12" viewBox="0 0 14 12"><path d="M1.5 6.5l4 4 7-9" stroke="#264d73" stroke-width="2.4" fill="none"/></svg>Aut odit aut fugit, sed quia</li>
    </ul>
    <div class="btn btn-navy" style="left:78px;top:346px;width:150px;height:46px">Signup</div>
  </div>
</section>

<section class="newsletter">
  <h2 class="section-title" style="top:68px">Newsletter</h2>
  <p class="abs center" style="left:0;width:1200px;top:156px;font-size:15px;line-height:27px;color:var(--ink)">Sed ut perspiciatis unde omnis iste natus error sit voluptatem accusantium<br>doloremque laudantium, totam rem aperiam,</p>
</section>
<div class="email-field">Enter Your Email :</div>
<div class="btn btn-navy" style="left:517px;top:4282px;width:166px;height:48px;font-size:16px">Submit</div>

<footer class="site-footer"></footer>
<div class="footer-brand"><span class="brand-dot" style="width:18px;height:18px"></span>HALVRA Q</div>
<nav class="footer-nav"><span>Home</span><span>About Us</span><span>O.R.T.</span><span>Lanternhall</span><span>Rise Onward</span><span>Halvra Q+</span><span>Testimonials</span></nav>
<div class="footer-contact" style="left:197px">
  <span class="ring"><svg width="16" height="20" viewBox="0 0 16 20"><path d="M8 1a6 6 0 016 6c0 4.5-6 12-6 12S2 11.5 2 7a6 6 0 016-6z" fill="none" stroke="#fff" stroke-width="1.6"/><circle cx="8" cy="7" r="2.2" fill="#fff"/></svg></span>
  <span>4820 Quarry Lane<br>Sample City</span>
</div>
<div class="footer-contact" style="left:521px">
  <span class="ring"><svg width="18" height="18" viewBox="0 0 24 24"><path fill="#fff" d="M6.6 10.8a15.1 15.1 0 006.6 6.6l2.2-2.2a1 1 0 011-.25 11.4 11.4 0 003.6.57 1 1 0 011 1V20a1 1 0 01-1 1A17 17 0 013 4a1 1 0 011-1h3.5a1 1 0 011 1c0 1.25.2 2.45.57 3.57a1 1 0 01-.25 1z"/></svg></span>
  <span>+1 555 014 2290</span>
</div>
<div class="footer-contact" style="left:758px">
  <span class="ring"><svg width="18" height="14" viewBox="0 0 18 14"><rect x="1" y="1" width="16" height="12" rx="2" fill="#fff"/><path d="M1.5 2l7.5 6 7.5-6" stroke="#264d73" stroke-width="1.6" fill="none"/></svg></span>
  <span>info@halvraq.ca</span>
</div>
<p class="copyright">Copyrights © 2022 Halvra Q All rights reserved.</p>

</body>
</html>
```